Bright Harbor Web Design & Marketing

Will award a 2nd place prize of $100.00 if someone can come up with a logo to match this design!
Updates

Okay, I'm really looking to see some better designs here. What do you think will bring the best designs out? Please remember with all future submissions I'm looking for a cartoon style / illustrator style website. I'm not sure what the technical term is for it, so I uploaded some images in the brief.

Target Market(s)

Small Business Owners

Industry/Entity Type

Marketing

Logo Text

BrightHarbor.com

Number of Pages Required

1 page

Colors

Designer to choose colors to be used in the design.

Requirements
Must have
• Logo should say BrightHarbor.com I would like more than just a text logo. I want some sort of cool custom graphic / icon with it that will look nice on shirts/hats/etc

```html
<!DOCTYPE html>
<html lang="en">
<head>
<meta charset="utf-8">
<title>Bright Harbor Web Design &amp; Marketing</title>
<link href="https://fonts.googleapis.com/css2?family=Maven+Pro:wght@400;500;700&family=Tinos:wght@400;700&display=swap" rel="stylesheet">
<style>
:root{
  --navy:#0e3447;
  --navy-deep:#0a2a3a;
  --teal:#12445b;
  --orange:#f7860f;
  --grey-bg:#f1f1f1;
  --text:#333;
  --muted:#666;
  --line:#d9d9d9;
  --white:#fff;
}
*{box-sizing:border-box;margin:0;padding:0}
html,body{width:1200px;height:4009px;overflow:hidden}
body{font-family:"Tinos",serif;color:var(--text);background:var(--white);position:relative}
.sans{font-family:"Maven Pro",sans-serif}
section,header,footer,nav{position:absolute;left:0;width:1200px}
.h2{font-family:"Maven Pro",sans-serif;font-weight:700;font-size:30px;color:var(--navy);text-align:center;letter-spacing:.5px}
.h2 span{color:var(--orange)}
.lead{font-size:13px;line-height:20px;color:var(--muted);text-align:center;width:920px;margin:0 auto}
.btn-call{display:inline-flex;align-items:center;gap:8px;background:var(--navy);color:var(--white);font-family:"Maven Pro",sans-serif;font-weight:700;font-size:15px;padding:0 18px 0 6px;height:36px;border-radius:18px}
.btn-call i{width:28px;height:28px;border-radius:50%;background:var(--orange);display:block}

/* header */
.site-header{top:0;height:86px;background:var(--white)}
.brand{position:absolute;left:150px;top:22px;display:flex;align-items:center;gap:10px}
.brand-dot{width:40px;height:40px;border-radius:50%;background:var(--orange)}
.brand-name{font-family:"Maven Pro",sans-serif;font-weight:700;font-size:28px;color:var(--navy)}
.header-phone{position:absolute;right:150px;top:28px;display:flex;align-items:center;gap:8px;font-family:"Maven Pro",sans-serif;font-weight:700;font-size:26px;color:var(--orange)}
.main-nav{top:86px;height:34px;background:var(--navy);display:flex;justify-content:center}
.main-nav ul{list-style:none;display:flex;width:900px;margin-left:0}
.main-nav li{flex:1;text-align:center;line-height:34px;font-family:"Maven Pro",sans-serif;font-size:13px;color:var(--white);border-right:1px solid rgba(255,255,255,.15)}
.main-nav li:last-child{border-right:0}
.main-nav li.active{background:var(--orange);flex:.55}

/* hero */
.hero{top:120px;height:473px;background:radial-gradient(ellipse at 60% 45%,#2f6fb0 0%,#174a86 35%,#0b2650 70%,#06163a 100%);text-align:center;color:var(--white)}
.hero-dot{width:52px;height:52px;border-radius:50%;background:var(--orange);margin:104px auto 10px}
.hero-name{font-family:"Maven Pro",sans-serif;font-weight:700;font-size:28px}
.hero-tag{font-family:"Maven Pro",sans-serif;font-weight:500;font-size:22px;margin-top:14px}
.hero .btn-call{margin-top:18px;background:var(--white);color:var(--navy)}
.hero-arrow{position:absolute;top:228px;width:26px;height:26px;background:rgba(255,255,255,.85)}
.hero-arrow.l{left:0}.hero-arrow.r{right:0}

/* about */
.about{top:593px;height:310px}
.about .h2{position:absolute;left:142px;top:40px;text-align:left}
.about-text{position:absolute;left:142px;top:100px;width:480px;font-size:12.5px;line-height:21px;color:var(--muted)}
.about-text p{margin-bottom:14px}
.laptop{position:absolute;left:690px;top:54px;width:350px;height:205px}
.laptop-screen{position:absolute;left:20px;top:0;width:310px;height:186px;background:#222;border-radius:10px 10px 0 0;padding:12px}
.laptop-screen div{width:100%;height:100%;background:#e9e9e9;display:flex;align-items:center;justify-content:center;gap:8px;font-family:"Maven Pro",sans-serif;font-weight:700;font-size:22px;color:var(--navy)}
.play{width:34px;height:34px;border-radius:50%;background:var(--navy)}
.laptop-base{position:absolute;left:0;top:186px;width:350px;height:14px;background:linear-gradient(#d8d8d8,#9a9a9a);border-radius:0 0 12px 12px}

/* services */
.services{top:903px;height:554px;background:var(--grey-bg)}
.services .h2{margin-top:50px}
.services .lead{margin-top:16px}
.svc-side{position:absolute;left:82px;top:190px}
.svc-side i{display:block;width:14px;height:14px;border-radius:50%;background:#5aa0d0;margin-bottom:16px}
.svc-menu{position:absolute;left:142px;top:185px;width:246px;list-style:none}
.svc-menu li{height:32px;line-height:30px;background:var(--navy);color:var(--white);font-family:"Maven Pro",sans-serif;font-size:11.5px;font-weight:500;padding-left:40px;border-bottom:2px solid #2a5367;position:relative}
.svc-menu li::before{content:"";position:absolute;left:10px;top:8px;width:18px;height:14px;border:1.5px solid rgba(255,255,255,.8);border-radius:2px}
.svc-menu li.active{background:var(--orange)}
.svc-icon{position:absolute;left:416px;top:178px}
.svc-detail{position:absolute;left:555px;top:200px;width:470px}
.svc-detail h3{font-family:"Maven Pro",sans-serif;font-size:15px;color:var(--navy);text-decoration:underline;margin-bottom:14px}
.svc-detail li{list-style:none;font-size:12px;line-height:16px;color:var(--muted);padding-left:28px;position:relative;margin-bottom:13px}
.svc-detail li svg{position:absolute;left:0;top:0}
.svc-answer{position:absolute;left:555px;top:370px}
.svc-answer p{font-family:"Maven Pro",sans-serif;font-weight:700;font-size:17px;color:var(--orange);margin:0 0 6px 16px}
.svc-answer .btn-call{height:28px;font-size:13px;width:300px}
.svc-answer .btn-call i{width:22px;height:22px}

/* cta */
.cta{top:1457px;height:222px;text-align:center}
.cta h2{font-family:"Maven Pro",sans-serif;font-weight:500;font-size:34px;color:var(--navy);margin-top:30px}
.cta p{font-size:19px;line-height:26px;color:#111;width:760px;margin:14px auto 16px}

/* pricing */
.pricing{top:1679px;height:665px;background:repeating-linear-gradient(90deg,#0f3d53 0 6px,#0c3347 6px 9px)}
.pricing-floor{position:absolute;left:0;bottom:0;width:1200px;height:232px;background:linear-gradient(#c79a63,#a6723f)}
.pricing .h2{color:var(--white);font-weight:500;margin-top:48px}
.plan{position:absolute;top:144px;width:204px;height:396px;background:var(--white);border-top:4px solid var(--orange);text-align:center;box-shadow:0 8px 18px rgba(0,0,0,.3)}
.plan.tall{top:132px;height:408px}
.plan-icon{width:52px;height:52px;border-radius:50%;border:3px solid var(--orange);margin:22px auto 12px;display:flex;align-items:center;justify-content:center}
.plan-icon i{width:24px;height:24px;border-radius:50%;background:var(--orange)}
.plan h3{font-family:"Maven Pro",sans-serif;font-weight:500;font-size:18px;color:#222}
.plan-from{font-size:12px;color:#888;margin-top:24px}
.plan-price{font-family:"Maven Pro",sans-serif;font-size:44px;color:#222;line-height:50px}
.plan-price sup{font-size:14px;vertical-align:22px}
.plan-price small{font-size:16px}
.plan ul{list-style:none;text-align:left;margin:14px 0 0 26px;font-size:12px;color:#444}
.plan li{line-height:26px}
.plan li::before{content:"›";margin-right:8px}
.plan-foot{position:absolute;left:0;bottom:0;width:100%;height:78px;background:#f1f1f1}
.plan-btn{display:inline-block;margin-top:12px;width:124px;height:30px;line-height:30px;font-family:"Maven Pro",sans-serif;font-size:13px;color:var(--white);background:var(--orange)}
.plan.dark .plan-btn{background:var(--navy)}
.plan-more{font-family:"Maven Pro",sans-serif;font-size:11px;color:#333;margin-top:8px}
.plan-more::after{content:"";display:inline-block;width:8px;height:8px;background:var(--orange);margin-left:22px}

/* clients */
.clients{top:2344px;height:249px}
.clients .h2{margin-top:42px}
.clients .lead{margin-top:14px}
.client-row{position:absolute;left:142px;top:170px;width:916px;display:flex;justify-content:space-between;align-items:center}
.client{display:flex;align-items:center;gap:5px;font-family:"Maven Pro",sans-serif;font-weight:700;font-size:15px;color:#222}
.client i{width:14px;height:14px;border-radius:50%;background:#222}
.client-arrow{position:absolute;top:176px;width:10px;height:10px;border-left:2px solid #aaa;border-bottom:2px solid #aaa}

/* why */
.why{top:2593px;height:502px;background:var(--grey-bg)}
.why .h2{margin-top:44px}
.why .lead{margin-top:14px}
.why-row{position:absolute;left:155px;top:147px;display:flex;gap:20px}
.why-item{width:160px;height:174px;background:var(--white);text-align:center;box-shadow:0 3px 8px rgba(0,0,0,.08);padding-top:16px}
.why-art{width:90px;height:88px;margin:0 auto 10px;border-radius:8px;background:linear-gradient(#fbd7a8,#f4a24a)}
.why-item.b .why-art{background:linear-gradient(#5a7d96,#0e3447)}
.why-item p{font-family:"Maven Pro",sans-serif;font-size:11px;line-height:14px;color:#222}
.why-info{position:absolute;left:155px;top:339px;width:890px;height:142px;background:var(--white);border-top:3px solid var(--navy);padding:14px 16px;font-size:12.5px;line-height:20px;color:var(--muted)}
.why-info::before{content:"";position:absolute;left:620px;top:-12px;border:8px solid transparent;border-bottom-color:var(--orange)}
.why-info h4{font-family:"Maven Pro",sans-serif;font-size:15px;color:var(--navy);margin-bottom:8px}

/* team */
.team{top:3095px;height:359px}
.team .h2{margin-top:42px}
.team .lead{margin-top:14px}
.member{position:absolute;top:161px;width:455px;height:178px;border:1px solid var(--line);background:var(--white)}
.member-photo{position:absolute;left:18px;top:-12px;width:66px;height:72px;background:linear-gradient(#c9ced3,#7b8692)}
.member h4{position:absolute;left:102px;top:10px;font-family:"Maven Pro",sans-serif;font-size:14px;color:var(--navy)}
.member .role{position:absolute;left:102px;top:30px;font-family:"Maven Pro",sans-serif;font-size:12px;color:var(--orange)}
.member p{position:absolute;left:18px;top:92px;width:420px;font-size:12.5px;line-height:19px;color:var(--muted)}
.team-arrow{position:absolute;top:244px;width:10px;height:10px;border-left:2px solid #aaa;border-bottom:2px solid #aaa}

/* inquiry */
.inquiry{top:3454px;height:403px;background:#f7f7f7}
.inquiry-photo{position:absolute;left:0;top:0;width:520px;height:403px;background:linear-gradient(90deg,#dfe3e6 0%,#eef0f1 70%,#f7f7f7 100%)}
.inquiry .h2{position:absolute;left:494px;top:52px;text-align:left}
.inquiry form{position:absolute;left:494px;top:110px;width:522px;font-family:"Maven Pro",sans-serif;font-size:11px;color:#444}
.field{position:absolute;height:46px;border-bottom:1px solid #ccc}
.field label{display:block;margin-bottom:4px}
.field.area{height:76px;border:1px solid #ccc;border-top:0;padding:0}
.field.area label{margin-bottom:16px}
.submit{position:absolute;left:0;top:230px;width:86px;height:28px;background:var(--navy);color:var(--white);font-size:12px;font-weight:700;text-align:center;line-height:28px}

/* footer */
.site-footer{top:3857px;height:152px;background:var(--navy-deep);color:var(--white);font-family:"Maven Pro",sans-serif}
.foot-col{position:absolute;top:32px;display:flex;gap:12px;font-size:11px;line-height:14px}
.foot-col b{display:block}
.foot-ring{width:36px;height:36px;border-radius:50%;border:2px solid var(--orange);flex:none;display:flex;align-items:center;justify-content:center}
.foot-bottom{position:absolute;left:222px;top:120px;width:860px;font-size:10px;color:#cfd8de}
.socials{position:absolute;right:0;top:-6px;display:flex;gap:8px}
.socials i{width:20px;height:20px;border-radius:50%;border:1px solid #b9c6cf}
</style>
</head>
<body>

<header class="site-header">
  <div class="brand"><span class="brand-dot"></span><span class="brand-name">BRIGHT Harbor</span></div>
  <div class="header-phone">
    <svg width="24" height="24" viewBox="0 0 24 24"><path d="M6.6 10.8a15 15 0 0 0 6.6 6.6l2.2-2.2a1 1 0 0 1 1-.25 11.4 11.4 0 0 0 3.6.57 1 1 0 0 1 1 1V20a1 1 0 0 1-1 1A17 17 0 0 1 3 4a1 1 0 0 1 1-1h3.5a1 1 0 0 1 1 1 11.4 11.4 0 0 0 .57 3.6 1 1 0 0 1-.25 1z" fill="#f7860f"/></svg>
    555-014-2288
  </div>
</header>

<nav class="main-nav">
  <ul>
    <li class="active">HOME</li>
    <li>SERVICES &amp; PRICING</li>
    <li>OUR TEAM</li>
    <li>CLIENTS</li>
    <li>CONTACT US</li>
  </ul>
</nav>

<section class="hero" role="img" aria-label="Blue network of glowing connected points">
  <div class="hero-dot"></div>
  <div class="hero-name">BRIGHT Harbor</div>
  <div class="hero-tag">The Design &amp; Marketing Team That Always Puts Trust &amp; Loyalty Before Profits</div>
  <span class="btn-call"><i></i>Call Us Today</span>
  <span class="hero-arrow l"></span><span class="hero-arrow r"></span>
</section>

<section class="about">
  <h2 class="h2">ABOUT BRIGHT <span>Harbor</span></h2>
  <div class="about-text">
    <p>We believe that honesty and integrity come before personal profits. We are a family owned and operated company. Our parents raised us to take care of each other and that's exactly what we've done. We treat each of our clients with the same loyalty and respect that we give each other.</p>
    <p>We are not looking to have hundreds and hundreds of clients. We are looking to expand our family with a handful of like-minded individuals. Companies who take pride in their work and their customers. We want to build mutually beneficial, lucrative, and long term partnerships.</p>
  </div>
  <div class="laptop">
    <div class="laptop-screen"><div><span class="play"></span>BRIGHT Harbor</div></div>
    <div class="laptop-base"></div>
  </div>
</section>

<section class="services">
  <h2 class="h2">SERVICES <span>We Provide</span></h2>
  <p class="lead">Lorem ipsum dolor sit amet, consectetuer adipiscing elit, sed diam nonummy nibh euismod tincidunt ut laoreet dolore magna aliquam erat volutpat. Ut wisi enim ad minim veniam, quis nostrud exerci.</p>
  <div class="svc-side"><i></i><i></i></div>
  <ul class="svc-menu">
    <li class="active">Website Design &amp; Management</li>
    <li>Logo Design &amp; Branding Materials</li>
    <li>Online Store Design &amp; Management</li>
    <li>Local Seo Management</li>
    <li>Search Engine Optimization</li>
    <li>Social Media Marketing</li>
    <li>Marketing Material &amp; Print Design</li>
    <li>Outsourcing Management</li>
    <li>Consulting Service</li>
  </ul>
  <svg class="svc-icon" width="116" height="104" viewBox="0 0 116 104">
    <rect x="4" y="8" width="96" height="66" rx="3" fill="none" stroke="#777" stroke-width="5"/>
    <rect x="44" y="74" width="16" height="16" fill="#777"/>
    <rect x="30" y="90" width="44" height="6" fill="#777"/>
    <path d="M108 4 L70 50" stroke="#777" stroke-width="7"/>
  </svg>
  <div class="svc-detail">
    <h3>Website Design &amp; Management</h3>
    <ul>
      <li><svg width="16" height="16"><rect x="1" y="1" width="14" height="14" fill="none" stroke="#0e3447" stroke-width="2"/><path d="M4 8l3 3 6-7" stroke="#0e3447" stroke-width="2" fill="none"/></svg>Lorem dolor sit amet, consectetuer adipiscing elit, sed diam nonummy nibh euismod</li>
      <li><svg width="16" height="16"><rect x="1" y="1" width="14" height="14" fill="none" stroke="#0e3447" stroke-width="2"/><path d="M4 8l3 3 6-7" stroke="#0e3447" stroke-width="2" fill="none"/></svg>Lorem dolor sit amet, consectetuer adipiscing</li>
      <li><svg width="16" height="16"><rect x="1" y="1" width="14" height="14" fill="none" stroke="#0e3447" stroke-width="2"/><path d="M4 8l3 3 6-7" stroke="#0e3447" stroke-width="2" fill="none"/></svg>Lorem dolor sit amet, consectetuer adipiscing elit, sed diam nonummy nibh euismod</li>
      <li><svg width="16" height="16"><rect x="1" y="1" width="14" height="14" fill="none" stroke="#0e3447" stroke-width="2"/><path d="M4 8l3 3 6-7" stroke="#0e3447" stroke-width="2" fill="none"/></svg>Lorem dolor sit amet, consectetuer adipiscing elit, sed diam nonummy nibh euismod.ornere dolor sit amet</li>
    </ul>
  </div>
  <div class="svc-answer">
    <p>We have answers</p>
    <span class="btn-call"><i></i>Call Us Today To Avail The Service</span>
  </div>
</section>

<section class="cta">
  <h2>Lorem ipsum dolor sit amet consectetuer</h2>
  <p>Lorem ipsum dolor sit amet consectetuer &nbsp;adipiscing elit sed diam the nonummy nibh sit amet consectetuer adipiscing elit sed consectetuer.</p>
  <span class="btn-call"><i></i>Call Us Today</span>
</section>

<section class="pricing">
  <div class="pricing-floor" role="img" aria-label="Wooden floor boards"></div>
  <h2 class="h2">OUR &nbsp;Pricing</h2>

  <div class="plan dark" style="left:160px">
    <div class="plan-icon"><i></i></div><h3>Basic Plan</h3>
    <div class="plan-from">Starting from</div>
    <div class="plan-price"><sup>$</sup>52<small>.95</small></div>
    <ul><li>Lorem Ipsum Dolar Ipsum</li><li>Lorem Ipsum Dolar</li><li>Lorem Ipsum Dolar Ipsum</li><li>Lorem Ipsum Dolar</li></ul>
    <div class="plan-foot"><span class="plan-btn">Get Started &nbsp;→</span><div class="plan-more">More Information</div></div>
  </div>
  <div class="plan tall" style="left:396px">
    <div class="plan-icon"><i></i></div><h3>Standard Plan</h3>
    <div class="plan-from">Starting from</div>
    <div class="plan-price"><sup>$</sup>114<small>.50</small></div>
    <ul><li>Lorem Ipsum Dolar Ipsum</li><li>Lorem Ipsum Dolar</li><li>Lorem Ipsum Dolar Ipsum</li><li>Lorem Ipsum Dolar</li></ul>
    <div class="plan-foot"><span class="plan-btn">Get Started &nbsp;→</span><div class="plan-more">More Information</div></div>
  </div>
  <div class="plan" style="left:623px">
    <div class="plan-icon"><i></i></div><h3>Gold Plan</h3>
    <div class="plan-from">Starting from</div>
    <div class="plan-price"><sup>$</sup>200<small>.95</small></div>
    <ul><li>Lorem Ipsum Dolar Ipsum</li><li>Lorem Ipsum Dolar</li><li>Lorem Ipsum Dolar Ipsum</li><li>Lorem Ipsum Dolar</li></ul>
    <div class="plan-foot"><span class="plan-btn">Get Started &nbsp;→</span><div class="plan-more">More Information</div></div>
  </div>
  <div class="plan tall" style="left:855px">
    <div class="plan-icon"><i></i></div><h3>Platinum Plan</h3>
    <div class="plan-from">Starting from</div>
    <div class="plan-price"><sup>$</sup>490<small>.00</small></div>
    <ul><li>Lorem Ipsum Dolar Ipsum</li><li>Lorem Ipsum Dolar</li><li>Lorem Ipsum Dolar Ipsum</li><li>Lorem Ipsum Dolar</li></ul>
    <div class="plan-foot"><span class="plan-btn">Get Started &nbsp;→</span><div class="plan-more">More Information</div></div>
  </div>
</section>

<section class="clients">
  <h2 class="h2">OUR <span>Valuable Clients</span></h2>
  <p class="lead">Lorem ipsum dolor sit amet, consectetuer adipiscing elit, sed diam nonummy nibh euismod tincidunt ut laoreet dolore magna aliquam erat volutpat. Ut wisi enim ad minim veniam, quis nostrud exerci.</p>
  <span class="client-arrow" style="left:112px;transform:rotate(45deg)"></span>
  <div class="client-row">
    <span class="client"><i></i>Tallmere</span>
    <span class="client">Quorvel</span>
    <span class="client">Quorvel</span>
    <span class="client">Pinewick</span>
    <span class="client"><i></i>Tallmere</span>
    <span class="client">Solvane</span>
    <span class="client">Brisco Labs</span>
    <span class="client">Brisco Labs</span>
  </div>
  <span class="client-arrow" style="left:1076px;transform:rotate(-135deg)"></span>
</section>

<section class="why">
  <h2 class="h2">WHY <span>CHoose Us</span></h2>
  <p class="lead">Lorem ipsum dolor sit amet, consectetuer adipiscing elit, sed diam nonummy nibh euismod tincidunt ut laoreet dolore magna aliquam erat volutpat. Ut wisi enim ad minim veniam, quis nostrud exerci.</p>
  <div class="why-row">
    <div class="why-item"><div class="why-art" role="img" aria-label="Hand holding a coin"></div><p>100% Risk Free<br>Investment</p></div>
    <div class="why-item b"><div class="why-art" role="img" aria-label="Hand holding a loyalty card"></div><p>Customer Loyalty<br>Program</p></div>
    <div class="why-item"><div class="why-art" role="img" aria-label="Support clock with 24/7 label"></div><p>24/7 U.S Based<br>Customer Support</p></div>
    <div class="why-item b"><div class="why-art" role="img" aria-label="Support agent at a desk"></div><p>Unmatched Personal<br>Service</p></div>
    <div class="why-item"><div class="why-art" role="img" aria-label="Payment option tiles"></div><p>Multiple Payment<br>Options Available</p></div>
  </div>
  <div class="why-info">
    <h4>Unmatched Personal Service</h4>
    <p>Do you need us to come to your office to help train staff on the management of your new website, content management system, or computer software?</p>
    <p>That's not a problem.</p>
    <p>We welcome to you and provide hands on training.</p>
  </div>
</section>

<section class="team">
  <h2 class="h2">OUR <span>Team</span></h2>
  <p class="lead">Lorem ipsum dolor sit amet, consectetuer adipiscing elit, sed diam nonummy nibh euismod tincidunt ut laoreet dolore magna aliquam erat volutpat. Ut wisi enim ad minim veniam, quis nostrud exerci.</p>
  <span class="team-arrow" style="left:112px;transform:rotate(45deg)"></span>
  <div class="member" style="left:152px">
    <div class="member-photo" role="img" aria-label="Portrait of team member"></div>
    <h4>DANIEL CORWEN</h4><div class="role">Chief Executive Officer</div>
    <p>Lorem ipsum dolor sit amet, consectetuer adipiscing elit, sed diam nonummy nibh euismod tincidunt ut laoreet dolore magna aliquam...[+]</p>
  </div>
  <div class="member" style="left:625px">
    <div class="member-photo" role="img" aria-label="Portrait of team member"></div>
    <h4>LUCAS BRENNARD</h4><div class="role">Chief Operations Officer</div>
    <p>Lorem ipsum dolor sit amet, consectetuer adipiscing elit, sed diam nonummy nibh euismod tincidunt ut laoreet dolore magna aliquam...[+]</p>
  </div>
  <span class="team-arrow" style="left:1076px;transform:rotate(-135deg)"></span>
</section>

<section class="inquiry">
  <div class="inquiry-photo" role="img" aria-label="Hands typing on a laptop at a white desk with a coffee cup and small plant"></div>
  <h2 class="h2">QUICK <span>Inquiry</span></h2>
  <form>
    <div class="field" style="left:0;top:0;width:250px"><label>First Name</label></div>
    <div class="field" style="left:272px;top:0;width:250px"><label>Last Name</label></div>
    <div class="field" style="left:0;top:56px;width:250px"><label>Email</label></div>
    <div class="field" style="left:272px;top:56px;width:250px"><label>Phone Number</label></div>
    <div class="field area" style="left:0;top:112px;width:522px"><label>Details About Your Enquiry</label></div>
    <div class="submit">SUBMIT</div>
  </form>
</section>

<footer class="site-footer">
  <div class="foot-col" style="left:220px">
    <span class="foot-ring"><svg width="14" height="18" viewBox="0 0 14 18"><path d="M7 0a7 7 0 0 0-7 7c0 5 7 11 7 11s7-6 7-11a7 7 0 0 0-7-7zm0 9.5A2.5 2.5 0 1 1 7 4.5a2.5 2.5 0 0 1 0 5z" fill="#f7860f"/></svg></span>
    <div><b>BRIGHT Harbor</b>Street Name, City Name<br>State Zip code</div>
  </div>
  <div class="foot-col" style="left:530px">
    <span class="foot-ring"><svg width="16" height="16" viewBox="0 0 24 24"><path d="M6.6 10.8a15 15 0 0 0 6.6 6.6l2.2-2.2a1 1 0 0 1 1-.25 11.4 11.4 0 0 0 3.6.57 1 1 0 0 1 1 1V20a1 1 0 0 1-1 1A17 17 0 0 1 3 4a1 1 0 0 1 1-1h3.5a1 1 0 0 1 1 1 11.4 11.4 0 0 0 .57 3.6 1 1 0 0 1-.25 1z" fill="#f7860f"/></svg></span>
    <div><b>Phone:</b>+555 0198 442</div>
  </div>
  <div class="foot-col" style="left:790px">
    <span class="foot-ring"><svg width="16" height="12" viewBox="0 0 16 12"><rect x="0.5" y="0.5" width="15" height="11" fill="none" stroke="#f7860f"/><path d="M0.5 0.5L8 7l7.5-6.5" fill="none" stroke="#f7860f"/></svg></span>
    <div><b>Email:</b>inquiry@brightharbor.com</div>
  </div>
  <div class="foot-bottom">Copyright © 2017 BRIGHT HARBOR. All Rights Reserved.
    <div class="socials"><i></i><i></i><i></i><i></i><i></i></div>
  </div>
</footer>

</body>
</html>
```